DL FLYER - Stroll Sip Nibble Trails

I need a2-sided DL flyer designed to put into Hotel foyers. This will need to stand out as it will be in a rack with multiple other options.

Our tours are all about walking with us to take in great venues for food and beverages with art and history along the way.

We operate in Perth City plus Fremantle.

I am hoping for the flyer to look something like my website - https://strollsipnibble.example.au/

This website will be updated in the coming weeks with new experiences and a new booking platform.

I want the flyers to be used to drive bookings from the updated website.

Attached are several images that could be used also.

Target Market(s)

Social groups, couples, friends groups & foodies!

Industry/Entity Type

Food & Beverage Walking Tours

Font styles to use
Serif
Sans Serif
Decorative
Script

Colors
0094D4
00A9DD
6FCCEA
C7EBF8
E9F6FB
59FF00
82FF00
B8FF75
E3FFCB
F4FFEA
FFF300
FFF600
FEFA6F
FFFEC7
FFFEE8
F0912C
F2A743
F7CA91
FBE8D2
FDF5EE

Requirements
Must have
• Logo and must look fun. Discount code - GOODVIBES for online price 15% off (not valid on gift voucher purchases)
Nice to have
• similar to my website - colours and styling. I will be updating available tours, costs and timing in the coming weeks. Check out my new booking link to get pricing and tour details - https://www-628q.reservly.example/reservly/b_strollsipnibbletrails_start.html?ctlsrc2=Qm482KTRVA9LZpd7JowsN3hbvY%2F5U8RaxtnBd%2FJqLm%3D&src=02r
Should not have
• .

```html
<!DOCTYPE html>
<html lang="en">
<head>
<meta charset="utf-8">
<title>Stroll Sip Nibble Trails – DL Flyer</title>
<link rel="stylesheet" href="https://fonts.googleapis.com/css2?family=Montserrat:wght@700;800;900&family=Quicksand:wght@500;600;700&family=Lilita+One&display=swap">
<style>
  :root{
    --bg:#b4b4b4;
    --cream:#f8f4e6;
    --pink:#f3d7d0;
    --orange:#ec6120;
    --mint:#9dd69e;
    --green:#19a06d;
    --ink:#1f2b2b;
    --white:#ffffff;
  }
  *{box-sizing:border-box;margin:0;padding:0}
  html,body{width:1200px;height:900px;overflow:hidden;background:var(--bg)}
  .canvas{position:relative;width:1200px;height:900px}
  .panel{position:absolute;top:45px;width:380px;height:810px;overflow:hidden;box-shadow:0 6px 18px rgba(0,0,0,.18)}
  .front{left:190px;background:var(--cream)}
  .back{left:630px;background:var(--mint)}
  .panel-art{position:absolute;inset:0}
  .head{font-family:"Montserrat",sans-serif;font-weight:900;text-transform:uppercase;line-height:1.02;letter-spacing:.5px}

  /* front */
  .logo{position:absolute;left:40px;top:34px;width:300px;text-align:center}
  .logo-scene{width:300px;height:150px;border-radius:50% 50% 18px 18px;background:linear-gradient(180deg,#e9efd9 0%,#bfe3c2 60%,#8fcf9f 100%)}
  .logo-name{margin-top:10px;display:flex;align-items:center;justify-content:center;gap:8px;font-family:"Montserrat",sans-serif;font-weight:900;font-size:22px;color:var(--green);line-height:1}
  .logo-dot{width:16px;height:16px;border-radius:50%;background:var(--orange)}
  .feature{position:absolute;font-size:22px}
  .f-explore{left:52px;top:478px;color:var(--ink)}
  .f-meet{left:218px;top:402px;color:var(--cream);text-align:right}
  .f-food{left:120px;top:680px;color:var(--pink);font-size:20px}
  .contact{position:absolute;left:0;right:0;top:722px;text-align:center;color:var(--white);font-family:"Montserrat",sans-serif}
  .contact p{font-weight:700;font-size:13px;letter-spacing:.6px;line-height:1.45}
  .contact .site{font-weight:900;font-size:18px;margin-top:2px}

  /* back */
  .about{position:absolute;left:30px;top:50px;width:320px;color:var(--ink)}
  .about h2{font-size:22px;margin-bottom:10px}
  .about p{font-family:"Quicksand",sans-serif;font-weight:600;font-size:11.4px;line-height:1.38;margin-bottom:8px}
  .badge-art{position:absolute;right:26px;top:22px;width:54px;height:46px;border-radius:50%;background:linear-gradient(135deg,#f7a36a,var(--orange))}
  .tours{position:absolute;left:0;top:325px;width:380px;height:315px;background:var(--pink);border-radius:0 0 40px 0}
  .tours-title{position:absolute;left:26px;top:-14px;background:var(--orange);color:var(--cream);font-size:20px;padding:8px 16px;border-radius:12px}
  .tour-list{position:absolute;left:26px;top:55px;width:330px;list-style:none}
  .tour{display:grid;grid-template-columns:140px 80px 1fr;align-items:center;min-height:58px}
  .tour-name{font-family:"Montserrat",sans-serif;font-weight:800;font-size:13.5px;line-height:1.1;color:var(--ink);text-transform:uppercase}
  .tour-price{font-family:"Lilita One",sans-serif;font-size:30px;color:var(--orange)}
  .tour-when{font-family:"Montserrat",sans-serif;font-weight:800;font-size:10px;line-height:1.15;color:var(--ink);text-transform:uppercase}
  .discount{position:absolute;left:0;right:0;top:672px;text-align:center;color:var(--ink)}
  .code-row{display:flex;align-items:center;justify-content:center;gap:10px}
  .code-label{font-size:14px;text-align:right}
  .code{background:var(--orange);color:var(--cream);font-size:30px;padding:6px 16px;border-radius:12px}
  .terms{font-family:"Quicksand",sans-serif;font-weight:600;font-size:12.5px;line-height:1.35;margin-top:8px}
</style>
</head>
<body>
<main class="canvas">

  <!-- front side -->
  <section class="panel front">
    <svg class="panel-art" viewBox="0 0 380 810" width="380" height="810" aria-hidden="true">
      <path d="M0,400 C60,310 240,300 270,390 C292,460 240,530 170,575 L0,690 Z" fill="var(--pink)"/>
      <path d="M380,200 L380,525 C320,505 210,512 160,530 C128,540 118,512 140,482 C178,425 205,370 212,300 C220,232 300,220 380,200 Z" fill="var(--orange)"/>
      <path d="M0,720 C90,620 200,560 380,540 L380,810 L0,810 Z" fill="var(--cream)"/>
    </svg>
    <svg class="panel-art" viewBox="0 0 380 810" width="380" height="810" role="img" aria-label="Photo of shared plates and dishes on a restaurant table">
      <defs>
        <linearGradient id="foodShade" x1="0" y1="0" x2="1" y2="1">
          <stop offset="0" stop-color="#5b5f5a"/>
          <stop offset="1" stop-color="#2f3a38"/>
        </linearGradient>
      </defs>
      <path d="M0,740 C90,640 200,582 380,560 L380,810 L0,810 Z" fill="url(#foodShade)"/>
    </svg>
    <svg class="panel-art" viewBox="0 0 380 810" width="380" height="810" aria-hidden="true">
      <path d="M0,790 C120,730 250,690 380,680 L380,810 L0,810 Z" fill="var(--green)"/>
      <!-- pin icon -->
      <circle cx="118" cy="430" r="44" fill="var(--mint)"/>
      <path d="M118,460 C104,444 96,432 96,420 A22,20 0 0 1 140,420 C140,432 132,444 118,460 Z" fill="none" stroke="var(--orange)" stroke-width="4" stroke-linejoin="round"/>
      <circle cx="118" cy="420" r="7" fill="var(--orange)"/>
      <!-- chat icon -->
      <circle cx="300" cy="335" r="42" fill="var(--mint)"/>
      <path d="M276,320 h48 a8,8 0 0 1 8,8 v14 a8,8 0 0 1 -8,8 h-28 l-12,10 v-10 h-8 a8,8 0 0 1 -8,-8 v-14 a8,8 0 0 1 8,-8 z" fill="none" stroke="var(--orange)" stroke-width="4" stroke-linejoin="round"/>
      <circle cx="289" cy="335" r="4" fill="var(--orange)"/>
      <circle cx="300" cy="335" r="4" fill="var(--orange)"/>
      <circle cx="311" cy="335" r="4" fill="var(--orange)"/>
      <!-- steaming bowl icon -->
      <circle cx="150" cy="628" r="42" fill="var(--mint)"/>
      <path d="M124,630 h52 c0,16 -12,26 -26,26 s-26,-10 -26,-26 z" fill="none" stroke="var(--orange)" stroke-width="4" stroke-linejoin="round"/>
      <path d="M138,620 c-6,-7 6,-11 0,-18 M152,620 c-6,-7 6,-11 0,-18 M166,620 c-6,-7 6,-11 0,-18" fill="none" stroke="var(--orange)" stroke-width="3" stroke-linecap="round"/>
    </svg>

    <div class="logo">
      <div class="logo-scene" role="img" aria-label="Illustration of a group of walkers in front of a city skyline"></div>
      <div class="logo-name"><span class="logo-dot"></span>Stroll Sip Nibble Trails</div>
    </div>

    <h3 class="feature head f-explore">Explore<br>the city</h3>
    <h3 class="feature head f-meet">Meet new<br>people</h3>
    <h3 class="feature head f-food">Enjoy great food</h3>

    <div class="contact">
      <p>0412 555 019</p>
      <p>PERTH@STROLLSIPNIBBLE.EXAMPLE.AU</p>
      <p class="site">STROLLSIPNIBBLE.EXAMPLE.AU</p>
    </div>
  </section>

  <!-- back side -->
  <section class="panel back">
    <div class="badge-art" role="img" aria-label="Small illustration of a cup and cutlery"></div>
    <div class="about">
      <h2 class="head">About us</h2>
      <p>Step off the tourist trail, leave the beaten track behind, do something different in a region near you and see the secret spots that locals love.</p>
      <p>We take our walking tours down the back streets, underneath and above plus through the alleyways, to share great food and beverages with our groups.</p>
      <p>Go with our guides to try modern Australian fare. All served with lashings of history about each city you tour.</p>
      <p>We have private tours for ready-made groups and our regular tours for people who are ready to mingle.</p>
    </div>

    <div class="tours">
      <h2 class="head tours-title">Tours &amp; Experiences</h2>
      <ul class="tour-list">
        <li class="tour"><span class="tour-name">Twilight tasting stroll</span><span class="tour-price">$85</span><span class="tour-when">Perth<br>Sat 4-7pm</span></li>
        <li class="tour"><span class="tour-name">Lazy harbour Sunday</span><span class="tour-price">$75</span><span class="tour-when">Fremantle<br>Sun 3-6pm</span></li>
        <li class="tour"><span class="tour-name">Grill &amp; ale ramble</span><span class="tour-price">$85</span><span class="tour-when">Perth<br>Sat 11am</span></li>
        <li class="tour"><span class="tour-name">Market basket wander</span><span class="tour-price">$80</span><span class="tour-when">Fremantle<br>Sat 1-4pm</span></li>
      </ul>
    </div>

    <div class="discount">
      <div class="code-row">
        <span class="head code-label">Discount<br>code</span>
        <span class="head code">GOODVIBES</span>
      </div>
      <p class="terms">for online price 15% off<br>(not valid on gift voucher purchases)</p>
    </div>
  </section>

</main>
</body>
</html>
```